verdant terraces simple classy business card design

my name is colin barrow and I run a gardening business aimed at high class verdant terraces. the business name is verdant terraces and our logo was designed on pixel harbour .My clientel are anything from residential homes to businesses. I take pride in my work and know that I offer a service like no other in my area.
The business card will be used to represent my business and I want it to be not only rememberable, but simplistic and modern. Eye catching too. Of course I would like it relatable to gardening and appealing to the correct clientel - those being garden enthusiasts, prestigious homes and businesses that are after top of the line gardening services like no other on the market.
I am not a typical lawn mowing business so I don't want a typical card design that represents that. The gardens I work with are generally million dollar properties with owners who are very garden proud looking for upkeep and guidance from me along with sometimes whole new garden designs. I want the business cards to show to my clients that I take pride, as they do, in their garden. And I want them to know from my card that I am a professional, qualified horticulturist offering them a top of the line service for life. I want them to refer my business on. I want them to look at my business card and see class and professionalism in a modern unique bold way.
The card should be simple with the possibility of the logo on the front being embossed/debossed and my details on the back the card should have a organic garden feel it's very important to me that it is absolutely perfect
I am also very open to ideas and suggestions so look forward to seeing the designs. the business logo has been supplied with this project and I want the card to be double sided

Contact info is
Colin Barrow - Managing Director / Horticulturist
Phone : 0481 526 704
Email: colinbarrow@verdantterraces.example.au

Target Market(s)

high class gardens residential and commercial

Industry/Entity Type

Gardener

Contact Information for Business Card

Contact info is
Phone : 0481 526 704

PLEASE MAKE CARD DOUBLE SIDED

Requirements
Must have
• organic simple classy modern feel
• must flow with the current logo that has been supplied with this project
• Double sided
• Must explain in a simple way that I deal with high end gardens and I'm a qualified horticulturist
Nice to have
• embossed debossed logo
Should not have
• shouldn't be to busy or cheap looking

```html
<!DOCTYPE html>
<html lang="en">
<head>
<meta charset="utf-8">
<title>Verdant Terraces – Business Card</title>
<link rel="stylesheet" href="https://fonts.googleapis.com/css2?family=Montserrat:wght@400;500;700&display=swap">
<style>
  :root {
    --backdrop: #2e2e2e;
    --card: #ffffff;
    --green: #4f9e4f;
    --green-deep: #3f8a3f;
    --emboss: #cfcfcf;
  }
  * { margin: 0; padding: 0; box-sizing: border-box; }
  html, body {
    width: 1200px;
    height: 900px;
    overflow: hidden;
    background: var(--backdrop);
    font-family: "Montserrat", Arial, sans-serif;
  }
  .canvas {
    position: relative;
    width: 1200px;
    height: 900px;
  }
  .card {
    position: absolute;
    left: 270px;
    width: 660px;
    height: 380px;
    background: var(--card);
    border-radius: 22px;
    overflow: hidden;
  }
  .card--front { top: 48px; }
  .card--back { top: 472px; }

  .card__band {
    position: absolute;
    left: 0;
    right: 0;
    bottom: 0;
    height: 18px;
    background: var(--green);
  }
  .card__band-notch {
    position: absolute;
    bottom: 0;
    left: 420px;
    width: 5px;
    height: 18px;
    background: var(--card);
  }

  .front__mark {
    position: absolute;
    top: 0;
    left: 0;
    right: 0;
    bottom: 18px;
    display: flex;
    align-items: center;
    justify-content: center;
  }
  .front__name {
    font-weight: 500;
    font-size: 38px;
    letter-spacing: 6px;
    text-transform: uppercase;
    color: var(--emboss);
  }

  .back__content {
    position: absolute;
    top: 0;
    left: 0;
    right: 0;
    bottom: 18px;
    display: flex;
    flex-direction: column;
    align-items: center;
    justify-content: center;
    text-align: center;
    color: var(--green);
  }
  .brand {
    display: flex;
    align-items: center;
    gap: 14px;
    margin-bottom: 22px;
  }
  .brand__dot {
    width: 22px;
    height: 22px;
    border-radius: 50%;
    background: var(--green);
  }
  .brand__name {
    font-weight: 500;
    font-size: 34px;
    letter-spacing: 5px;
    text-transform: uppercase;
    color: var(--green);
  }
  .person__name {
    font-weight: 700;
    font-size: 26px;
    color: var(--green-deep);
  }
  .person__role {
    font-weight: 400;
    font-size: 16px;
    margin-top: 4px;
  }
  .contact__icons {
    display: flex;
    gap: 8px;
    margin-top: 14px;
  }
  .contact__icons svg { width: 14px; height: 14px; }
  .contact__line {
    font-weight: 400;
    font-size: 17px;
    margin-top: 6px;
  }
</style>
</head>
<body>
<main class="canvas">
  <section class="card card--front" aria-label="Card front">
    <div class="front__mark">
      <span class="front__name">Verdant Terraces</span>
    </div>
    <div class="card__band"><span class="card__band-notch"></span></div>
  </section>

  <section class="card card--back" aria-label="Card back">
    <div class="back__content">
      <div class="brand">
        <span class="brand__dot"></span>
        <span class="brand__name">Verdant Terraces</span>
      </div>
      <p class="person__name">Colin Barrow</p>
      <p class="person__role">Managing Director / Horticulturist</p>
      <div class="contact__icons">
        <svg viewBox="0 0 24 24" aria-label="Phone">
          <path fill="var(--green)" d="M6.6 10.8a15 15 0 0 0 6.6 6.6l2.2-2.2a1 1 0 0 1 1-.25 11.4 11.4 0 0 0 3.6.57 1 1 0 0 1 1 1V20a1 1 0 0 1-1 1A17 17 0 0 1 3 4a1 1 0 0 1 1-1h3.5a1 1 0 0 1 1 1c0 1.25.2 2.45.57 3.57a1 1 0 0 1-.25 1z"/>
        </svg>
        <svg viewBox="0 0 24 24" aria-label="Email">
          <rect x="3" y="5" width="18" height="14" rx="1.5" fill="none" stroke="var(--green)" stroke-width="2"/>
          <path d="M3.5 6l8.5 7 8.5-7" fill="none" stroke="var(--green)" stroke-width="2"/>
        </svg>
      </div>
      <p class="contact__line">0481 526 704</p>
      <p class="contact__line">colinbarrow@verdantterraces.example.au</p>
    </div>
    <div class="card__band"><span class="card__band-notch"></span></div>
  </section>
</main>
</body>
</html>
```